Create a wordpress website for Tovarin business solution

This project is to create a complete website with all pages.

Overview
The purpose of this project is to create a full complete website with all pages (16 pages). The site should be professional and modern. The site is for an IT recruiting and IT training company. The site needs to be easy to administer and update content. It should be simple to add pages, videos and testimonials later. I will leave the site layout, color schemes and flow to the designers.

Navigation Menu (Home, who we are, what we do, what makes us different, why it matters, candidate portal, contact us, Blog)

WHO WE ARE should be a drop down menu with link to pages (about us, mission, vision and purpose, our team)

WHAT WE DO should be drop down menu with link to the following pages (IT Recruiting, IT Training, Hardware and software sales)

What makes us different should be single page with different paragraph titles. (We live what we do, we don't compromise quality, we share knowledge, staffing guarantee)

Why it matters should be single page with paragraph titles. (Quickly fill positions, candidate career development)

Candidate portal should links to my portal login page. I can add the correct URL later. I just need it to link to somewhere. I can change it.

Contact us should have (address, phone number, google map and a form to submit request for a call back)

Blog - This link should launch a wordpress blogging module

Target Market(s)

IT RECRUITING AND CONSULTING

Industry/Entity Type

It Company

Coding

Coded - Design and coding required

Requirements
Must have
• Company Logo
• Navigation Menu (Home, who we are, what we do, what makes us different, why it matters, candidate portal, contact us)
• WHO WE ARE should be a drop down menu with link to pages (about us, mission, vision and purpose, our team)
• WHAT WE DO should be drop down menu with link to the following pages (IT Recruiting, IT Training, Hardware and software sales)
• What makes us different should be single page with different paragraph titles. (We live what we do, we don't compromise quality, we share knowledge, staffing guarantee)
• Why it matters should be single page with paragraph titles. (Quickly fill positions, candidate career development)
• Candidate portal should links to my portal login page. I can add the correct URL later. I just need it to link to somewhere. I can change it.
• Contact us should have (address, phone number, google map and a form to submit request for a call back)

```html
<!DOCTYPE html>
<html lang="en">
<head>
<meta charset="utf-8">
<title>Tovarin Business Solution</title>
<link href="https://fonts.googleapis.com/css2?family=Montserrat:wght@300;400;500;600;700&family=Open+Sans:wght@400;600&display=swap" rel="stylesheet">
<style>
:root{
  --orange:#e8730c;
  --orange-dark:#c95b05;
  --orange-btn:#f0901c;
  --blue:#0a5aa6;
  --blue-dark:#08498a;
  --navy:#1f5d96;
  --ink:#3c3c3c;
  --grey:#8a8a8a;
  --soft:#f2f2f2;
  --line:#dcdcdc;
  --white:#ffffff;
}
*{margin:0;padding:0;box-sizing:border-box}
html,body{width:1200px;height:2719px;overflow:hidden;background:var(--white)}
body{position:relative;font-family:'Montserrat',sans-serif;color:var(--ink)}
.abs{position:absolute}

/* header */
.brand{left:145px;top:30px}
.brand-name{font-size:42px;font-weight:600;color:var(--navy);letter-spacing:-0.5px;line-height:1}
.brand-sub{font-size:11px;font-weight:500;color:var(--orange);letter-spacing:1.6px;margin-top:6px;padding-left:6px}
.nav{left:0;top:114px;width:1200px;height:46px;background:var(--orange)}
.nav ul{list-style:none;display:flex;position:absolute;left:140px;top:0;height:46px}
.nav li{font-size:15px;color:var(--white);line-height:46px;padding:0 8px}
.nav li.active{background:var(--orange-dark);padding:0 19px}

/* hero */
.hero{left:0;top:160px;width:1200px;height:522px;background:linear-gradient(135deg,#5a5652 0%,#3e3b38 45%,#6b6660 100%)}
.hero-title{left:0;top:338px;width:1200px;text-align:center;color:var(--white);font-size:51px;font-weight:400;letter-spacing:1.5px}
.hero-sub{left:0;top:402px;width:1200px;text-align:center;color:var(--white);font-size:27px;font-weight:400;letter-spacing:1px}
.hero-btn{left:526px;top:460px;width:150px;height:40px;border:2px solid var(--white);color:var(--white);font-size:14px;text-align:center;line-height:36px}
.dots{left:561px;top:641px;display:flex;gap:9px}
.dots span{width:15px;height:15px;border-radius:50%;background:var(--white)}
.dots span.off{background:transparent;border:2px solid var(--white)}

/* what we do */
.section-title{width:1200px;left:0;text-align:center;font-size:29px;font-weight:400;color:#444}
.services{left:112px;top:765px;width:976px;height:272px}
.service{position:absolute;top:0;width:310px;color:var(--white)}
.service h3{font-size:18px;font-weight:500;line-height:24px;margin-top:18px}
.service p{font-family:'Open Sans',sans-serif;font-size:12px;line-height:20px;opacity:.9;margin-top:8px}
.service .btn{display:inline-block;margin-top:14px;border:1.5px solid var(--white);font-size:10px;font-weight:600;padding:0 18px;line-height:26px}

/* who we are */
.who-title{left:138px;top:1130px;font-size:29px;color:var(--orange);font-weight:400}
.who-text{left:141px;top:1187px;width:470px;font-family:'Open Sans',sans-serif;font-size:14.5px;line-height:24.5px;color:#555}
.btn-orange{left:141px;top:1340px;width:118px;height:34px;background:var(--orange-btn);color:var(--white);font-size:11px;font-weight:600;text-align:center;line-height:34px;border-radius:2px}
.who-art{left:616px;top:1124px;width:440px;height:250px;background:radial-gradient(ellipse at center,#dbe9fa 0%,#f3f8fe 60%,#ffffff 100%)}

/* about band */
.band{left:0;top:1465px;width:1200px;height:498px;background:linear-gradient(180deg,#eeeeef,#f7f7f7)}
.cards{left:138px;top:1519px;width:926px;height:390px;background:var(--white);border:1px solid var(--line)}
.card{position:absolute;top:0;width:308.6px;height:388px;text-align:center}
.card + .card{border-left:1px solid var(--line)}
.card-img{position:absolute;left:0;top:0;width:100%;height:158px;color:var(--white);font-size:23px;font-weight:500;display:flex;align-items:center;justify-content:center;line-height:28px;padding-top:30px}
.card p{position:absolute;top:180px;left:50px;right:50px;font-family:'Open Sans',sans-serif;font-size:13.5px;line-height:23.5px;color:#999}
.card .more{position:absolute;top:340px;left:0;width:100%;font-size:14px;font-weight:600;color:var(--orange)}

/* blogs */
.blog-img{width:174px;height:174px;border-radius:50%}
.blog h4{font-size:16px;font-weight:600;color:#222}
.blog p{font-family:'Open Sans',sans-serif;font-size:13px;line-height:23.5px;color:#999;margin-top:8px;width:250px}
.blog .more{font-size:13px;font-weight:500;color:var(--blue);margin-top:8px}

/* footer */
.footer{left:0;top:2330px;width:1200px;height:389px;background:var(--soft)}
.f-col h5{font-size:17px;font-weight:600;color:var(--blue);margin-bottom:10px}
.f-col li{list-style:none;font-family:'Open Sans',sans-serif;font-size:13.5px;line-height:24.5px;color:#555}
.contact-row{display:flex;align-items:flex-start;gap:10px;font-family:'Open Sans',sans-serif;font-size:13.5px;line-height:20px;color:#555}
.ico{width:32px;height:32px;border-radius:50%;border:1.5px solid #9aa3ad;display:flex;align-items:center;justify-content:center;flex:none}
.divider{left:145px;top:2605px;width:925px;height:1px;background:var(--line)}
.copy{left:0;top:2626px;width:1200px;text-align:center;font-family:'Open Sans',sans-serif;font-size:12.5px;color:#777}
.social{left:496px;top:2663px;display:flex;gap:14px}
.social span{width:34px;height:34px;border-radius:50%;background:var(--white);border:1px solid #e2e2e2}
</style>
</head>
<body>

<header>
  <div class="abs brand">
    <div class="brand-name">tovarin</div>
    <div class="brand-sub">BUSINESS SOLUTION LLC</div>
  </div>
  <nav class="abs nav">
    <ul>
      <li class="active">Home</li>
      <li>Who we are</li>
      <li>What we do</li>
      <li>What makes us different</li>
      <li>Why it matters</li>
      <li>Candidate portal</li>
      <li>Contact us</li>
      <li>Blog</li>
    </ul>
  </nav>
</header>

<section>
  <div class="abs hero" role="img" aria-label="Photo of a trainer presenting to a seated group in a bright office"></div>
  <h1 class="abs hero-title">IT TRAINING &amp; RECRUITING</h1>
  <h2 class="abs hero-sub">PROIN ORCI ODIO COMMODO GRAVIDA</h2>
  <div class="abs hero-btn">START NOW</div>
  <div class="abs dots"><span class="off"></span><span></span><span></span><span></span></div>
</section>

<section>
  <h2 class="abs section-title" style="top:713px">WHAT WE DO</h2>
  <div class="abs services">
    <svg width="976" height="272" style="position:absolute;left:0;top:0">
      <polygon points="29,0 976,0 947,272 0,272" fill="#0a5aa6"/>
      <polygon points="237,0 529,0 500,272 208,272" fill="#08498a"/>
      <!-- icons -->
      <g fill="none" stroke="#fff" stroke-width="3">
        <circle cx="82" cy="66" r="22"/><circle cx="82" cy="66" r="14"/>
        <line x1="82" y1="38" x2="82" y2="50"/><line x1="82" y1="82" x2="82" y2="94"/>
        <line x1="54" y1="66" x2="66" y2="66"/><line x1="98" y1="66" x2="110" y2="66"/>
        <rect x="380" y="50" width="32" height="32" rx="3"/>
        <rect x="388" y="58" width="16" height="16"/>
        <line x1="386" y1="42" x2="386" y2="50"/><line x1="396" y1="42" x2="396" y2="50"/><line x1="406" y1="42" x2="406" y2="50"/>
        <line x1="386" y1="82" x2="386" y2="90"/><line x1="396" y1="82" x2="396" y2="90"/><line x1="406" y1="82" x2="406" y2="90"/>
        <rect x="685" y="40" width="40" height="26" stroke-width="2"/>
        <line x1="695" y1="66" x2="690" y2="86" stroke-width="2"/>
        <circle cx="702" cy="78" r="5" stroke-width="2"/><circle cx="718" cy="78" r="5" stroke-width="2"/><circle cx="734" cy="78" r="5" stroke-width="2"/>
        <line x1="694" y1="92" x2="742" y2="92" stroke-width="2"/>
      </g>
    </svg>
    <div class="service" style="left:52px;top:100px">
      <h3>IT Recruiting</h3>
      <p>Pellentesque nibh libero ultricies eu sagittis<br>non mollis sed justo Praesent metu Curabitur<br>vel mi sit amet magna malesuada</p>
      <span class="btn">READ MORE</span>
    </div>
    <div class="service" style="left:376px;top:100px">
      <h3>Hardware and<br>Software Sales</h3>
      <p>Pellentesque nibh libero ultricies eu sagittis<br>non mollis sed justo Praesent metu</p>
      <span class="btn">READ MORE</span>
    </div>
    <div class="service" style="left:678px;top:100px">
      <h3>IT Training</h3>
      <p>Pellentesque nibh libero ultricies eu sagittis<br>non mollis sed justo Praesent metus non<br>mollis sed justo Praesent metu</p>
      <span class="btn">READ MORE</span>
    </div>
  </div>
</section>

<section>
  <h2 class="abs who-title">WHO WE ARE</h2>
  <p class="abs who-text">consectetuer augue nisi quis lacus Ut ac mi quis lacus mollis aliquam Curabitur iaculis tempus eros Curabitur vel mi sit amet ultrices Ut nisi erat fermentum vel congue id euismod in elit Fusce ultricies orci ac feugiat suscipit leo massa sodales velit et scelerisque mi tortor at ipsum Proin orci odio</p>
  <div class="abs btn-orange">READ MORE</div>
  <div class="abs who-art" role="img" aria-label="Line illustration of a magnifying glass over a network of people icons"></div>
</section>

<section>
  <div class="abs band" role="img" aria-label="Light grey background with faint circuit lines"></div>
  <div class="abs cards">
    <div class="card" style="left:0">
      <div class="card-img" role="img" aria-label="Blue-toned photo of a team with a rocket icon" style="background:linear-gradient(135deg,#2a6aa8,#1b4f82)">OUR MISSION</div>
      <p>Curabitur vel mi sit amet magna malesuada ultrices Ut nisi erat fermentum vel congue id euismod in elit Fusce ultricies orci ac feugiat suscipit leo massa sodales velit et scelerisque mi tortor at ipsum cligula</p>
      <div class="more">READ MORE &rsaquo;</div>
    </div>
    <div class="card" style="left:308.6px">
      <div class="card-img" role="img" aria-label="Orange-toned photo of colleagues with a light bulb icon" style="background:linear-gradient(135deg,#f19a2c,#de7a12)">WHAT MAKES US<br>DIFFERENT</div>
      <p>Curabitur vel mi sit amet magna malesuada ultrices Ut nisi erat fermentum vel congue id euismod in elit Fusce ultricies orci ac feugiat suscipit leo massa sodales velit et scelerisque mi tortor at ipsum cligula</p>
      <div class="more">READ MORE &rsaquo;</div>
    </div>
    <div class="card" style="left:617.2px">
      <div class="card-img" role="img" aria-label="Amber-toned photo of a group with a people icon" style="background:linear-gradient(135deg,#c58428,#9c6414)">OUR TEAM</div>
      <p>Curabitur vel mi sit amet magna malesuada ultrices Ut nisi erat fermentum vel congue id euismod in elit Fusce ultricies orci ac feugiat suscipit leo massa sodales velit et scelerisque mi tortor at ipsum cligula</p>
      <div class="more">READ MORE &rsaquo;</div>
    </div>
  </div>
</section>

<section>
  <h2 class="abs section-title" style="top:2020px">OUR BLOGS</h2>
  <div class="abs blog-img" style="left:138px;top:2076px;background:linear-gradient(135deg,#b9b4ad,#6f6a64)" role="img" aria-label="Photo of people seated in a meeting"></div>
  <div class="abs blog" style="left:323px;top:2090px">
    <h4>Etiam est nunc venenatis</h4>
    <p>magna malesuada ultrices Ut nisi erat fermentum vel congue id euismod in elit Fusce ultricies orci ac feugiat suscipit leo massa sodales velit et scelerisq</p>
    <div class="more">READ MORE</div>
  </div>
  <div class="abs blog-img" style="left:596px;top:2076px;background:linear-gradient(135deg,#9fb4c8,#3f5366)" role="img" aria-label="Photo of two professionals shaking hands"></div>
  <div class="abs blog" style="left:785px;top:2090px">
    <h4>Curabitur vel mi sit amet</h4>
    <p>magna malesuada ultrices Ut nisi erat fermentum vel congue id euismod in elit Fusce ultricies orci ac feugiat suscipit leo massa sodales velit et scelerisq</p>
    <div class="more">READ MORE</div>
  </div>
</section>

<footer>
  <div class="abs footer"></div>
  <div class="abs f-col" style="left:158px;top:2396px">
    <h5>COMPANY</h5>
    <ul><li>Home</li><li>About</li><li>What we do</li><li>Team</li></ul>
  </div>
  <div class="abs f-col" style="left:328px;top:2396px">
    <h5>MARKETS</h5>
    <ul><li>Training</li><li>Marketing</li><li>Createive Design</li><li>Media Buying</li></ul>
  </div>
  <div class="abs f-col" style="left:522px;top:2396px">
    <h5>RESOURCES</h5>
    <ul><li>Team</li><li>Support</li><li>FAQ</li><li>Contact</li></ul>
  </div>
  <div class="abs f-col" style="left:700px;top:2396px;width:330px">
    <h5>CONTACT US</h5>
    <div class="contact-row">
      <span class="ico"><svg width="12" height="16" viewBox="0 0 12 16"><path d="M6 0a6 6 0 0 0-6 6c0 4.5 6 10 6 10s6-5.5 6-10a6 6 0 0 0-6-6z" fill="#1f4f7e"/><circle cx="6" cy="6" r="2.2" fill="#fff"/></svg></span>
      <span>Fernwick House, 12 Alderbrook Lane, Marlow, Kentshire, KM3 8TD, United Kingdom</span>
    </div>
    <div class="contact-row" style="margin-top:10px;align-items:center">
      <span class="ico"><svg width="14" height="14" viewBox="0 0 14 14"><path d="M3 0.5l2.2 3-1.3 1.6c.8 1.8 2.2 3.2 4 4l1.6-1.3 3 2.2-1.2 2.6C6 12.4 1.6 8 .5 2z" fill="#1f4f7e"/></svg></span>
      <span>+44 (0) 7000 418275</span>
    </div>
    <div class="contact-row" style="margin-top:8px;align-items:center">
      <span class="ico"><svg width="14" height="10" viewBox="0 0 14 10"><rect width="14" height="10" rx="1" fill="#1f4f7e"/><path d="M0.5 0.8L7 5.5l6.5-4.7" stroke="#fff" stroke-width="1.2" fill="none"/></svg></span>
      <span>info@tovarinsolutions.example</span>
    </div>
  </div>
  <div class="abs divider"></div>
  <div class="abs copy">&copy; 2016 Company Name &nbsp;All right reserved &nbsp;Term of Use</div>
  <div class="abs social"><span></span><span></span><span></span><span></span></div>
</footer>

</body>
</html>
```